We need a complete design for our construction company KELTO CONSTRUCTION based in Auckland New Zealand, we need a logo, website, business card, vehicle design etc..
We are a mid to high-end construction company who work mostly on residential projects and some commercial.

What we want to see in the design;
Professional,
Architectural,
Simple,
Alternative,

We want the design to communicate professionalism, high quality wormanship and and quality service.

Target Market(s)

People looking for a quality building/ construction company

Industry/Entity Type

Construction Company

Contact Information for Business Card

KELTO CONSTRUCTION.co.nz
Lino Verasek
lino@keltoconstruction.example.nz
021 5807 462

Logo Text

KELTO CONSTRUCTION

Number of Pages Required

5+ page

Font styles to use
Sans Serif

Colors

Designer to choose colors to be used in the design.

Requirements
Must have
• Must appear high end, professional, quality, be simple, easy to use, give security to potential clients
Nice to have
• high-quality photos of our recent projects
• about us page
• blog page
• contact us page
• high quality content
Should not have
• should not be hard to use and have too much going on.

```html
<!DOCTYPE html>
<html lang="en">
<head>
<meta charset="utf-8">
<title>Kelto Construction</title>
<link href="https://fonts.googleapis.com/css2?family=Roboto:ital,wght@0,400;0,500;0,700;1,400;1,500&display=swap" rel="stylesheet">
<style>
:root{
  --green:#1f5a3c;
  --green-dark:#173f2c;
  --gold:#d9a21c;
  --gold-band:#c99a1e;
  --ink:#2a2a2a;
  --body:#555;
  --light:#f3f3f3;
  --footer:#1c1c1c;
  --footer-deep:#111;
  --white:#fff;
}
*{box-sizing:border-box;margin:0;padding:0}
html,body{width:1200px;height:3327px;overflow:hidden}
body{font-family:'Roboto',sans-serif;color:var(--body);background:var(--white);position:relative}
.abs{position:absolute}
.center{text-align:center}

/* hero */
.hero{left:0;top:0;width:1200px;height:680px;background:linear-gradient(180deg,#2b3440 0%,#3a4756 45%,#1d242c 100%)}
.hero-cut{left:0;top:600px;width:1200px;height:80px}
.brand{left:100px;top:30px;display:flex;align-items:center;gap:14px;color:var(--white);font-weight:700;font-size:30px;line-height:1}
.brand .mark{width:56px;height:56px;border:3px solid var(--white);border-radius:50%}
.brand small{display:block;font-size:22px;font-weight:700}
.top-contact{right:100px;top:36px;display:flex;gap:26px;color:var(--white);font-size:16px;align-items:center}
.top-contact span{display:flex;align-items:center;gap:10px}
.ico-ring{width:28px;height:28px;border:2px solid var(--white);border-radius:50%;display:flex;align-items:center;justify-content:center}
.nav{right:100px;top:88px;display:flex;gap:42px;font-size:17px;font-weight:500;color:var(--white);text-transform:uppercase}
.hero-title{left:0;top:310px;width:1200px;font-size:52px;font-weight:700;color:var(--white)}
.hero-sub{left:250px;top:380px;width:700px;font-size:17px;line-height:27px;color:var(--white)}
.btn{background:var(--gold);color:var(--white);font-weight:500;text-transform:uppercase;display:flex;align-items:center;justify-content:center}
.hero-btn{left:537px;top:448px;width:124px;height:36px;font-size:16px;border-radius:2px}
.dots{display:flex;gap:8px}
.dots i{width:11px;height:11px;border-radius:50%;background:var(--white);display:block}
.dots i.on{box-shadow:0 0 0 3px rgba(255,255,255,.5) ;background:transparent;border:2px solid var(--white)}
.hero-dots{left:569px;top:514px}

/* welcome */
.welcome{left:0;top:665px;width:1200px;height:590px;background:linear-gradient(120deg,#fff 0%,#faf6ec 55%,#f3ead2 100%)}
.h2{left:0;width:1200px;font-size:32px;font-weight:700;color:var(--ink);text-transform:uppercase}
.lead{left:128px;top:786px;width:944px;font-size:13px;line-height:25px}
.service{width:300px;text-align:center}
.service .circle{width:124px;height:124px;border-radius:50%;background:var(--green);border:4px solid var(--white);box-shadow:0 0 0 3px var(--green);margin:0 auto;display:flex;align-items:center;justify-content:center}
.service h3{margin-top:28px;font-size:17px;font-weight:500;color:var(--ink);text-transform:uppercase;letter-spacing:.3px}
.service p{margin-top:12px;font-size:13px;line-height:24px}
.service .chev{margin-top:8px}

/* projects */
.projects{left:0;top:1255px;width:1200px;height:703px;background:var(--light)}
.grid{left:98px;top:1400px;width:1002px;height:456px;display:grid;grid-template-columns:repeat(3,1fr);grid-template-rows:repeat(2,1fr);gap:3px}
.photo{display:block}
.promo{background:var(--green);color:var(--white);text-align:center;padding-top:40px}
.promo h4{font-size:20px;font-weight:700;text-transform:uppercase}
.promo p{font-size:13px;line-height:21px;margin:10px auto 0;width:270px}
.promo .outline{display:inline-block;margin-top:20px;border:1px solid var(--white);padding:7px 12px;font-size:12px;font-weight:500}

/* testimonials */
.testi{left:0;top:1958px;width:1200px;height:352px;background:linear-gradient(180deg,var(--gold-band) 0%,#c6961b 70%,#a98323 100%)}
.rule{height:2px;background:var(--white)}
.quote{left:195px;top:2108px;width:810px;font-size:14px;line-height:24px;font-style:italic;color:var(--white)}
.author{left:0;top:2196px;width:1200px;font-size:16px;font-weight:500;font-style:italic;color:var(--white)}
.bars{left:562px;top:2256px;display:flex;gap:4px}
.bars i{display:block;width:22px;height:3px;background:rgba(255,255,255,.45)}
.bars i.on{background:var(--white)}

/* blog */
.blog-rule{left:575px;top:2444px;width:50px;height:2px;background:var(--ink)}
.post-big{left:106px;top:2495px;width:435px;height:240px}
.caption{left:106px;top:2754px;font-size:17px;color:var(--ink)}
.meta{font-size:12px;color:#444;display:flex;gap:12px;align-items:center}
.post-side{left:568px;width:173px;height:145px}
.side-text{left:763px;width:340px}
.side-text h5{font-size:17px;font-weight:400;color:var(--ink)}
.side-text .meta{margin-top:14px;font-size:13px}
.side-text p{margin-top:12px;font-size:13px;line-height:23px}

/* footer */
.footer{left:0;top:2905px;width:1200px;height:338px;background:var(--footer)}
.copy{left:0;top:3243px;width:1200px;height:84px;background:var(--footer-deep);color:#ccc;font-size:13px;display:flex;align-items:center;justify-content:center}
.f-brand{left:100px;top:3005px;display:flex;align-items:center;gap:12px;color:var(--white);font-weight:700;font-size:28px;line-height:1}
.f-brand .mark{width:50px;height:50px;border:3px solid var(--white);border-radius:50%}
.f-brand small{display:block;font-size:20px}
.socials{left:100px;top:3105px;display:flex;gap:6px}
.socials i{display:block;width:24px;height:24px;border:1.5px solid var(--white);border-radius:50%}
.f-head{font-size:20px;font-weight:700;color:var(--white);text-transform:uppercase}
.links{list-style:none;font-size:14px;color:var(--white)}
.links li{height:25px;display:flex;align-items:center;gap:14px}
.contact-row{display:flex;gap:18px;color:var(--white);font-size:13px;line-height:20px}
.contact-row b{font-weight:700;font-size:14px}
.hex{width:36px;height:36px;flex:none}
.field{border:1px solid #ccc;color:#ddd;font-size:12px;padding:8px 10px}
.submit{left:800px;top:3143px;width:107px;height:34px;font-size:15px;font-weight:700;border-radius:3px}
</style>
</head>
<body>

<!-- hero -->
<div class="abs hero" role="img" aria-label="Dusk photo of a modern glass office tower"></div>
<svg class="abs hero-cut" viewBox="0 0 1200 80" preserveAspectRatio="none" aria-hidden="true"><path d="M0 10 Q600 70 1200 0 L1200 80 L0 80 Z" fill="#fff"/></svg>
<div class="abs brand"><span class="mark"></span><div>Kelto<small>Construction</small></div></div>
<div class="abs top-contact">
  <span><span class="ico-ring"><svg width="14" height="14" viewBox="0 0 24 24"><path d="M6 2l4 4-2 3c1 3 4 6 7 7l3-2 4 4-3 4C10 21 3 14 2 5z" fill="#fff"/></svg></span>01632 960 415</span>
  <span><span class="ico-ring"><svg width="14" height="12" viewBox="0 0 24 18"><rect x="1" y="1" width="22" height="16" fill="none" stroke="#fff" stroke-width="2"/><path d="M1 1l11 9 11-9" fill="none" stroke="#fff" stroke-width="2"/></svg></span>info@keltoconstruction.example.com</span>
</div>
<nav class="abs nav"><span>Home</span><span>About Us</span><span>Projects</span><span>Blog</span><span>Contact Us</span></nav>
<h1 class="abs hero-title center">KELTO CONSTRUCTION</h1>
<p class="abs hero-sub center">Sed ut perspiciatis unde omnis iste natus error sit voluptatem accusantium doloremque laudantium, totam rem aperiam, eaque ipsa quae</p>
<div class="abs btn hero-btn">Read More</div>
<div class="abs dots hero-dots"><i class="on"></i><i></i><i></i><i></i></div>

<!-- welcome -->
<section class="abs welcome" role="img" aria-label="Faint photo of a builder on a warm yellow backdrop"></section>
<h2 class="abs h2 center" style="top:732px">Welcome to Kelto Construction</h2>
<p class="abs lead center">Sed ut perspiciatis unde omnis iste natus error sit voluptatem accusantium doloremque laudantium, totam rem aperiam, eaque ipsa quae ab illo inventore veritatis et quasi architecto beatae vitae dicta sunt explicabo. Nemo enim ipsam voluptatem quia voluptas sit aspernatur aut odit aut fugit, sed quia consequuntur magni dolores eos qui ratione voluptatem sequi nesciunt. Neque porro quisquam doloremque laudantium, totam rem aperiam</p>

<div class="abs service" style="left:112px;top:900px">
  <div class="circle"><svg width="56" height="56" viewBox="0 0 56 56" fill="none" stroke="#fff" stroke-width="2.5"><rect x="8" y="14" width="40" height="36"/><path d="M4 16L28 4l24 12"/><rect x="14" y="20" width="6" height="6"/><rect x="25" y="20" width="6" height="6"/><rect x="36" y="20" width="6" height="6"/><rect x="14" y="31" width="6" height="6"/><rect x="36" y="31" width="6" height="6"/><rect x="24" y="36" width="8" height="14"/></svg></div>
  <h3>Kelto Building Services</h3>
  <p>Sed ut perspiciatis unde omnis iste natus error sit voluptatem accusantium doloremque laudantium, totam rem aperiam, eaque ipsa quae</p>
  <svg class="chev" width="14" height="12" viewBox="0 0 14 12" fill="none" stroke="#333" stroke-width="1.6"><path d="M2 1l5 4 5-4M2 6l5 4 5-4"/></svg>
</div>
<div class="abs service" style="left:444px;top:900px">
  <div class="circle"><svg width="56" height="56" viewBox="0 0 56 56" fill="none" stroke="#fff" stroke-width="2.5"><path d="M12 6h24l10 10v34H12z"/><path d="M36 6v10h10"/><path d="M18 24h20M18 31h20M18 38h12"/></svg></div>
  <h3>Property Management</h3>
  <p>Sed ut perspiciatis unde omnis iste natus error sit voluptatem accusantium doloremque laudantium, totam rem aperiam, eaque ipsa quae</p>
  <svg class="chev" width="14" height="12" viewBox="0 0 14 12" fill="none" stroke="#333" stroke-width="1.6"><path d="M2 1l5 4 5-4M2 6l5 4 5-4"/></svg>
</div>
<div class="abs service" style="left:786px;top:900px">
  <div class="circle"><svg width="56" height="56" viewBox="0 0 56 56" fill="#fff"><path d="M24 6h8l10 38H14z"/><rect x="8" y="44" width="40" height="6"/><rect x="19" y="20" width="18" height="4" fill="#1f5a3c"/><rect x="17" y="31" width="22" height="4" fill="#1f5a3c"/></svg></div>
  <h3>Reliable Contractors</h3>
  <p>Sed ut perspiciatis unde omnis iste natus error sit voluptatem accusantium doloremque laudantium, totam rem aperiam, eaque ipsa quae</p>
  <svg class="chev" width="14" height="12" viewBox="0 0 14 12" fill="none" stroke="#333" stroke-width="1.6"><path d="M2 1l5 4 5-4M2 6l5 4 5-4"/></svg>
</div>

<!-- projects -->
<section class="abs projects"></section>
<h2 class="abs h2 center" style="top:1313px">Recent Projects</h2>
<div class="abs grid">
  <div class="photo" role="img" aria-label="Brick family home with green lawn" style="background:linear-gradient(180deg,#3f7fd0 0%,#8db4de 40%,#8a5a44 60%,#4f9a2c 100%)"></div>
  <div class="photo" role="img" aria-label="Timber and stone two-storey house" style="background:linear-gradient(180deg,#86b4e4 0%,#b8c5cf 35%,#8c6a4c 65%,#6d8a4c 100%)"></div>
  <div class="photo" role="img" aria-label="Suburban house with flower garden" style="background:linear-gradient(180deg,#3a86d6 0%,#9fc1e2 35%,#b9a48e 60%,#4f8a3a 100%)"></div>
  <div class="photo" role="img" aria-label="Lit house with pool at dusk" style="background:linear-gradient(180deg,#1c3f78 0%,#2e5385 40%,#a8784a 62%,#3a6fa0 100%)"></div>
  <div class="photo" role="img" aria-label="Row of townhouses with picket fence" style="background:linear-gradient(180deg,#1c55b8 0%,#5f8fd4 35%,#d8cf9e 60%,#4c7f2e 100%)"></div>
  <div class="promo">
    <h4>Kelto Construction</h4>
    <p>Sed ut perspiciatis unde omnis iste natus error sit voluptatem accusantium doloremque laudantium, totam rem aperiam, eaque ipsa quae</p>
    <span class="outline">READ MORE</span>
  </div>
</div>

<!-- testimonials -->
<section class="abs testi" role="img" aria-label="City skyline tinted in gold"></section>
<h2 class="abs h2 center" style="top:2026px;color:#fff">Testimonials</h2>
<div class="abs rule" style="left:565px;top:2080px;width:70px"></div>
<p class="abs quote center">“ Sed ut perspiciatis unde omnis iste natus error sit voluptatem accusantium doloremque laudantium, totam rem aperiam, eaque ipsa quae ab illo inventore veritatis et quasi architecto beatae vitae dicta sunt explicabo. Nemo enim ipsam voluptatem quia voluptas sit aspernatur aut odit aut fugit, sed quia consequuntur magni dolores eos qui ratione voluptatem</p>
<p class="abs author center">Mara Tennick – Kelto Construction</p>
<div class="abs bars"><i class="on"></i><i></i><i></i></div>

<!-- blog -->
<h2 class="abs h2 center" style="top:2384px">Latest Blog</h2>
<div class="abs blog-rule"></div>
<div class="abs post-big" role="img" aria-label="Modern white apartment block under blue sky" style="background:linear-gradient(180deg,#2d78c9 0%,#8fb9e3 40%,#e6e3dc 55%,#b8b0a2 80%,#6a8e3c 100%)"></div>
<p class="abs caption">Nemo enim ipsam voluptatem quia voluptas</p>
<div class="abs meta" style="left:106px;top:2790px">
  <span>▦ JULY 05, 2018</span><span style="font-size:11px">3 MINUTES AGO</span><span>/</span><span style="font-size:11px">0 COMMENTS</span>
</div>

<div class="abs post-side" style="top:2495px" role="img" aria-label="White residential tower with lawn" style="" ></div>
<div class="abs post-side" style="top:2495px;background:linear-gradient(180deg,#c7d4dc 0%,#e7e8e5 50%,#7c9c58 100%)"></div>
<div class="abs side-text" style="top:2500px">
  <h5>Nemo enim ipsam voluptatem quia</h5>
  <div class="meta">▦ JULY 05, 2018</div>
  <p>Lorem ipsum dolor sit amet, consectetur adipiscing elit, sed do eiusmod tempor incididunt ut labore et dolore magna aliqua. Ut enim ad minim veniam</p>
</div>
<div class="abs post-side" style="top:2668px;background:linear-gradient(135deg,#2b5fa6 0%,#5d86c0 45%,#e9e2d8 70%,#c9572c 100%)" role="img" aria-label="Hands holding a small model house over plans"></div>
<div class="abs side-text" style="top:2673px">
  <h5>Nemo enim ipsam voluptatem quia</h5>
  <div class="meta">▦ JULY 05, 2018</div>
  <p>Lorem ipsum dolor sit amet, consectetur adipiscing elit, sed do eiusmod tempor incididunt ut labore et dolore magna aliqua. Ut enim ad minim veniam</p>
</div>

<!-- footer -->
<footer class="abs footer"></footer>
<div class="abs f-brand"><span class="mark"></span><div>Kelto<small>Construction</small></div></div>
<div class="abs socials"><i></i><i></i><i></i><i></i><i></i></div>

<h4 class="abs f-head" style="left:330px;top:2960px">Quick Links</h4>
<ul class="abs links" style="left:330px;top:3010px">
  <li><span>›</span>Home</li><li><span>›</span>About us</li><li><span>›</span>Projects</li><li><span>›</span>Blog</li><li><span>›</span>Contact us.</li>
</ul>

<h4 class="abs f-head" style="left:523px;top:2960px">Contact Us</h4>
<div class="abs contact-row" style="left:523px;top:3012px">
  <svg class="hex" viewBox="0 0 36 36"><path d="M18 1l15 8.5v17L18 35 3 26.5v-17z" fill="none" stroke="#fff" stroke-width="1.5"/><path d="M18 10a5 5 0 015 5c0 4-5 10-5 10s-5-6-5-10a5 5 0 015-5z" fill="#fff"/></svg>
  <div><b>KELTO CONSTRUCTION</b><br>48 Harbour View Rd, Ponsonby,<br>Auckland 1011, NZ</div>
</div>
<div class="abs contact-row" style="left:523px;top:3084px">
  <svg class="hex" viewBox="0 0 36 36"><path d="M18 1l15 8.5v17L18 35 3 26.5v-17z" fill="none" stroke="#fff" stroke-width="1.5"/><rect x="14" y="10" width="8" height="16" rx="1.5" fill="none" stroke="#fff" stroke-width="1.8"/></svg>
  <div><b>PHONE:</b><br><b style="font-size:15px">09-555-0184</b></div>
</div>
<div class="abs contact-row" style="left:523px;top:3142px">
  <svg class="hex" viewBox="0 0 36 36"><path d="M18 1l15 8.5v17L18 35 3 26.5v-17z" fill="none" stroke="#fff" stroke-width="1.5"/><rect x="11" y="13" width="14" height="10" fill="#fff"/></svg>
  <div><b>Mail:</b><br>info@keltoconstruction.example.com</div>
</div>

<h4 class="abs f-head" style="left:800px;top:2960px">Get In Touch</h4>
<div class="abs field" style="left:800px;top:3014px;width:146px;height:38px">Name</div>
<div class="abs field" style="left:954px;top:3014px;width:146px;height:38px">Phone</div>
<div class="abs field" style="left:800px;top:3060px;width:300px;height:70px">Message</div>
<div class="abs btn submit">SUBMIT</div>

<div class="abs copy">Copyright © 2018 Kelto Construction. All Right Reserved</div>

</body>
</html>
```